Children’s entertainer/balloon artist Website Home Page and custom landing page

I need a home page design for the home page of a children and family entertainer/balloon twister’s website. I also need a custom landing page for family theatre shows performed by the same entertainer.
It will be a Wordpress website and I need the final artwork in a layer Photoshop file with all the layers clearly named and labeled.

Target Market(s)

The site visitors are mainly mums, aged between early 20’s and late 30’s. Other visitors will included companies for Christmas functions, and event organisers for corporate functions.

Industry/Entity Type

Entertainment

Number of Pages Required

2 page

Font styles to use
Sans Serif

Colors
34a6d7
f37122

Requirements
Must have
• Layout
• I have included a wireframe for the home page layout and the custom landing page for your reference. This is a guide only and I welcome your interpretation with the rough layout provided.
• This website needs to look good on all devices as it will be fully responsive.
• It needs to include a footer area on the page, that has social media and a call to action area included.
• Colours
• The main colours for the site is:
• orange (call to action colour)
• ff6800
• blue/turquoise
• 42abc3
• Pictures
• I have included images of the entertainer/balloon artist for you to use/take inspiration from.
• These images will be included on the website. I want to show lots of people having fun.
• I would like to have elements of the logo used in isolation across the website
• i.e. the octopus figure to be included in the footer or the bird element to be included in the testimonial slider etc.
• Elements to include
• Note: use the images of the entertainer in the boxes on the home page (balloon shows, balloon twisting, balloon workshops, theatre shows (the three little balloon pigs on his head)
Nice to have
Should not have
• Element to avoid
• Stock imagery of balloon sculptures - use images provided.

```html
<!DOCTYPE html>
<html lang="en">
<head>
<meta charset="utf-8">
<title>Benny Bop – Children's Entertainer & Balloon Twister</title>
<link rel="stylesheet" href="https://fonts.googleapis.com/css2?family=Open+Sans:ital,wght@0,400;0,600;0,700;1,700&display=swap">
<style>
:root{
  --blue:#34a6d7;
  --blue-dark:#1f86b5;
  --orange:#f37122;
  --orange-dark:#d95c12;
  --page:#eef1f3;
  --white:#ffffff;
  --ink:#3d4449;
  --muted:#7c868d;
  --footer:#2f3a42;
  --footer-dark:#232c32;
  --line:#dde3e7;
}
*{box-sizing:border-box;margin:0;padding:0}
html,body{width:705px;height:1200px;overflow:hidden}
body{font-family:"Open Sans",Arial,sans-serif;color:var(--ink);background:var(--page);position:relative;font-size:7px;line-height:1.45}
.abs{position:absolute}

/* header */
.top-strip{left:0;top:0;width:705px;height:30px;background:var(--white)}
.social-top{left:557px;top:6px;display:flex;gap:4px}
.social-top span{width:15px;height:15px;border-radius:50%;background:#d9342b;display:block}
.call-now{left:612px;top:7px;font-size:11px;font-weight:700;color:var(--orange)}
.call-now small{font-size:8px;color:var(--muted);font-weight:600;margin-right:3px}
.nav-bar{left:0;top:58px;width:705px;height:32px;background:var(--white);box-shadow:0 2px 4px rgba(0,0,0,.12)}
.nav{left:96px;top:58px;height:32px;display:flex;align-items:center;gap:0}
.nav a{font-size:8px;font-weight:600;color:var(--ink);text-decoration:none;padding:0 12px;height:32px;line-height:32px;border-right:1px solid var(--line)}
.nav a.active{color:var(--blue);border-bottom:3px solid var(--blue)}
.logo{left:14px;top:6px;width:78px;height:100px;display:flex;flex-direction:column;align-items:center;justify-content:center;gap:5px;z-index:3}
.logo .dot{width:46px;height:46px;border-radius:50%;background:var(--blue)}
.logo .name{font-size:14px;font-weight:700;color:var(--orange);line-height:1}

/* hero */
.hero-band{left:0;top:90px;width:705px;height:260px;background:linear-gradient(#f7f9fa,#e6ebee)}
.hero{left:94px;top:100px;width:517px;height:228px;border-radius:4px;background:linear-gradient(120deg,#1a3f7a 0%,#2f6fb6 45%,#6fb2e4 75%,#f0b35a 100%);box-shadow:0 3px 8px rgba(0,0,0,.25)}
.hero-title{left:124px;top:140px;font-size:21px;font-style:italic;font-weight:700;color:var(--white);line-height:1.2;text-shadow:0 2px 3px rgba(0,0,0,.3)}

/* testimonials */
.section-title{font-size:13px;font-weight:400;color:var(--ink)}
.section-title b{color:var(--blue);font-weight:600}
.testi-title{left:42px;top:352px}
.testi-line{left:42px;top:372px;width:470px;height:1px;background:var(--line)}
.avatar{left:42px;top:385px;width:34px;height:34px;border-radius:50%;background:#b7c3cb}
.testi-text{left:86px;top:384px;width:420px;color:var(--muted);font-size:7px}
.testi-dots{left:250px;top:430px;display:flex;gap:4px}
.testi-dots i{width:5px;height:5px;border-radius:50%;background:#c6cfd5;display:block}
.testi-dots i:first-child{background:var(--blue)}
.mascot-promo{left:548px;top:344px;width:120px;height:150px;border-radius:6px;background:linear-gradient(#7fc6ea,var(--blue))}
.promo-text{left:560px;top:448px;width:96px;text-align:center;font-size:7px;font-weight:700;color:var(--white)}
.btn{display:inline-block;background:var(--orange);color:var(--white);font-weight:700;font-size:7px;padding:3px 8px;border-radius:2px;text-decoration:none}
.promo-btn{left:586px;top:472px}

/* welcome */
.welcome-band{left:0;top:500px;width:705px;height:160px;background:var(--white)}
.welcome-title{left:40px;top:512px}
.welcome-line{left:40px;top:532px;width:430px;height:1px;background:var(--line)}
.welcome-text{left:40px;top:541px;width:430px;color:var(--muted)}
.welcome-text p{margin-bottom:6px}
.welcome-text a{color:var(--orange);font-weight:600;text-decoration:none}
.profile{left:486px;top:510px;width:178px;height:138px;border:1px solid var(--line);background:#fafbfc;padding:6px}
.profile-head{display:flex;gap:6px;align-items:center}
.profile-head .pic{width:26px;height:26px;background:#c9d3d9}
.profile-head b{font-size:7px;color:var(--ink)}
.profile-grid{display:grid;grid-template-columns:repeat(4,1fr);gap:4px;margin-top:8px}
.profile-grid span{height:26px;background:linear-gradient(#8eb4cf,#4f7c9c)}

/* service cards */
.cards{left:38px;top:694px;display:flex;gap:12px}
.card{width:148px;height:190px;background:var(--white);box-shadow:0 2px 5px rgba(0,0,0,.15);padding:6px}
.card h3{font-size:10px;font-weight:600;color:var(--blue);text-align:center;margin-bottom:5px}
.card .photo{height:70px}
.card .info{background:var(--blue);color:var(--white);padding:6px;height:90px;text-align:center;font-size:6.5px}
.card .info .btn{margin-top:6px}
.p1{background:linear-gradient(135deg,#3a73b8,#e8a55a)}
.p2{background:linear-gradient(135deg,#d8544a,#f5c06b)}
.p3{background:linear-gradient(135deg,#3c8fbf,#f2d06b)}
.p4{background:linear-gradient(135deg,#7a4fa0,#f39ab2)}

/* call to action */
.cta{left:40px;top:912px;width:510px;height:52px;background:var(--orange);clip-path:polygon(0 0,100% 0,96% 50%,100% 100%,0 100%,4% 50%)}
.cta-text{left:72px;top:920px;width:320px;font-size:10.5px;font-weight:600;color:var(--white);line-height:1.3}
.cta-btn{left:420px;top:930px;background:var(--white);color:var(--orange);font-size:8px;padding:4px 10px}
.mascot-footer{left:560px;top:880px;width:112px;height:112px;border-radius:8px;background:linear-gradient(#8fd0ef,var(--blue))}

/* footer */
.footer{left:0;top:998px;width:705px;height:186px;background:var(--footer)}
.wave{left:0;top:978px}
.fcol{top:1012px;color:#b9c3ca}
.fcol h4{font-size:9px;font-weight:600;color:var(--white);margin-bottom:8px}
.fcol ul{list-style:none}
.fcol li{margin-bottom:4px;font-size:7px}
.col1{left:40px}
.col2{left:200px;width:120px}
.col2 .field{height:13px;background:var(--white);border-radius:2px;margin-bottom:5px;color:#9aa4ab;padding:2px 4px;font-size:6.5px}
.col2 .field.tall{height:28px}
.col3{left:352px;width:140px}
.col3 li{display:flex;gap:5px;align-items:flex-start}
.col3 svg{flex:none;margin-top:1px}
.col4{left:520px}
.col4 li{display:flex;align-items:center;gap:6px}
.col4 li span{width:13px;height:13px;border-radius:50%;background:var(--blue);display:block}
.bottom-bar{left:0;top:1184px;width:705px;height:16px;background:var(--footer-dark);color:#8f9aa2;font-size:6.5px;line-height:16px;padding-left:40px}
</style>
</head>
<body>

<header>
  <div class="abs top-strip"></div>
  <div class="abs social-top"><span></span><span></span><span></span></div>
  <div class="abs call-now"><small>Call Now</small>555-014-2270</div>
  <div class="abs nav-bar"></div>
  <nav class="abs nav">
    <a class="active" href="#">Home</a>
    <a href="#">Balloon Shows</a>
    <a href="#">Balloon Decoration</a>
    <a href="#">Theatre</a>
    <a href="#">Reviews</a>
    <a href="#">Contact</a>
  </nav>
  <div class="abs logo"><span class="dot"></span><span class="name">Benny Bop</span></div>
</header>

<section>
  <div class="abs hero-band"></div>
  <div class="abs hero" role="img" aria-label="Photo of the entertainer holding colourful balloon sculptures"></div>
  <h1 class="abs hero-title">Hilariously funny balloon<br>shows &amp; balloon<br>twisting</h1>
</section>

<section>
  <h2 class="abs section-title testi-title">Client <b>Testimonials</b></h2>
  <div class="abs testi-line"></div>
  <div class="abs avatar" role="img" aria-label="Client portrait"></div>
  <p class="abs testi-text">Benny made our party a day to remember. The children laughed from start to finish and every single child went home with their very own balloon animal. He was friendly, punctual and brilliant with the little ones. We have already booked him again for next year and would recommend him to any family.</p>
  <div class="abs testi-dots"><i></i><i></i><i></i></div>
  <div class="abs mascot-promo" role="img" aria-label="Blue mascot character holding a sign"></div>
  <div class="abs promo-text">Book Benny for Your Next Function</div>
  <a class="abs btn promo-btn" href="#">Book Now</a>
</section>

<section>
  <div class="abs welcome-band"></div>
  <h2 class="abs section-title welcome-title">Welcome to <b>Benny Bop</b></h2>
  <div class="abs welcome-line"></div>
  <div class="abs welcome-text">
    <p>Benny is a family entertainer and balloon twister who brings laughter, colour and fun to birthday parties, school fairs, festivals and corporate events. Every show is packed with silly jokes, giant balloon creations and plenty of chances for the audience to join in. Whether it is a small gathering at home or a large Christmas function, Benny tailors each performance to the age of the children and the size of the crowd, so everyone leaves smiling.</p>
    <p>From balloon workshops to theatre shows, there is something for every family. Get in touch today to check availability for your date and start planning a party nobody will forget. <a href="#">Read More</a></p>
  </div>
  <aside class="abs profile">
    <div class="profile-head"><span class="pic" role="img" aria-label="Profile photo"></span><b>Benny Bop<br><span style="font-weight:400;color:var(--muted)">Family entertainer</span></b></div>
    <div class="profile-grid" role="img" aria-label="Gallery of party photos">
      <span></span><span></span><span></span><span></span>
      <span></span><span></span><span></span><span></span>
    </div>
  </aside>
</section>

<section class="abs cards">
  <article class="card">
    <h3>Balloon Shows</h3>
    <div class="photo p1" role="img" aria-label="Entertainer performing a balloon show"></div>
    <div class="info">Fast, funny and full of surprises, our balloon shows keep children laughing from the very first minute.<br><a class="btn" href="#">Read More</a></div>
  </article>
  <article class="card">
    <h3>Balloon Twisting</h3>
    <div class="photo p2" role="img" aria-label="Balloon twisting for children at a party"></div>
    <div class="info">Swords, dogs, flowers and crowns twisted on the spot for every guest to take home after the party.<br><a class="btn" href="#">Read More</a></div>
  </article>
  <article class="card">
    <h3>Balloon Workshops</h3>
    <div class="photo p3" role="img" aria-label="Children learning balloon modelling in a workshop"></div>
    <div class="info">Hands-on sessions where children learn to make their own balloon models with simple, playful steps.<br><a class="btn" href="#">Read More</a></div>
  </article>
  <article class="card">
    <h3>Theatre Shows</h3>
    <div class="photo p4" role="img" aria-label="Theatre show with three balloon pigs"></div>
    <div class="info">Family theatre full of music, stories and balloon characters, perfect for venues and festival stages.<br><a class="btn" href="#">Read More</a></div>
  </article>
</section>

<section>
  <div class="abs cta"></div>
  <p class="abs cta-text">Contact Now for More Detail and make your Next Functions memorable</p>
  <a class="abs btn cta-btn" href="#">Book Now</a>
</section>

<footer>
  <svg class="abs wave" width="705" height="24" viewBox="0 0 705 24" aria-hidden="true"><path d="M0 24 C180 0 420 4 705 14 L705 24 Z" fill="#2f3a42"/></svg>
  <div class="abs footer"></div>
  <div class="abs mascot-footer" role="img" aria-label="Mascot character with glasses"></div>
  <div class="abs fcol col1">
    <h4>Quick Links</h4>
    <ul><li>Home</li><li>Balloon Shows</li><li>Balloon Decoration</li><li>Theatre</li><li>Reviews</li><li>Contact</li></ul>
  </div>
  <div class="abs fcol col2">
    <h4>Contact Now</h4>
    <div class="field">Name</div>
    <div class="field">Email</div>
    <div class="field tall">Message</div>
    <span class="btn">Submit</span>
  </div>
  <div class="abs fcol col3">
    <h4>Contact Detail</h4>
    <ul>
      <li><svg width="8" height="10" viewBox="0 0 8 10"><path d="M4 0a4 4 0 0 1 4 4c0 3-4 6-4 6S0 7 0 4a4 4 0 0 1 4-4z" fill="#34a6d7"/><circle cx="4" cy="4" r="1.5" fill="#2f3a42"/></svg><span><b style="color:#fff">Benny Bop</b><br>12 Maple Lane, Sunnyvale<br>Parkton PT1 4XY</span></li>
      <li><svg width="9" height="9" viewBox="0 0 9 9"><path d="M2 0l2 2-1 1.5a6 6 0 0 0 2.5 2.5L7 5l2 2-1.5 2C4 9 0 5 0 1.5z" fill="#34a6d7"/></svg>Phone: (555) 014-2270</li>
      <li><svg width="9" height="7" viewBox="0 0 9 7"><rect width="9" height="7" rx="1" fill="#34a6d7"/><path d="M0 0l4.5 4L9 0" stroke="#2f3a42" fill="none"/></svg>hello@bennybop.example</li>
    </ul>
  </div>
  <div class="abs fcol col4">
    <h4>Follow Us</h4>
    <ul><li><span></span>Friends Page</li><li><span></span>Quick Updates</li><li><span></span>Work Network</li></ul>
  </div>
  <div class="abs bottom-bar">Copyright © 2015 Benny Bop. All rights reserved.</div>
</footer>

</body>
</html>
```